Marrowby Water Taxi and Transport Business Card

I need business cards for my new water taxi and freight transport business I have started here in Kodiak Alaska. Kodiak is a remote island in the middle of the gulf of Alaska. There are seven native villages around the island and Kodiak is the #2 fishing port in the United States. We also have the largest Coast Guard Base in the U.S. My company will be providing water taxi and freight transport logistics to the villages and many hunting and fishing lodges as well as remote properties around the island.

I would like a business card that isn't status quo, something that stands out, either in feel or appearance. I do like clean minimal designs but it needs to have the necessary contact info on it.

Target Market(s)

remote lodge / property owners, residents of the many villages around Kodiak and any one wanting to enjoy the great outdoors of Kodiak Alaska

Industry/Entity Type

Business

Contact Information for Business Card

I like clean simple designs that aren't cluttered but still provide the necessary information

Colors
0255a3
3277b5
33a4d5
9bcb3c
add136
fbed22
ffc214
f78f20
f37122

Requirements
Must have
• logo and contact info
• Captain Mason Elwick
• www.marrowbyferryline.com
• mason@marrowbyferryline.com

```html
<!DOCTYPE html>
<html lang="en">
<head>
<meta charset="utf-8">
<title>Marrowby Water Taxi and Transport – Business Card</title>
<link rel="stylesheet" href="https://fonts.googleapis.com/css2?family=Questrial&family=Montserrat:wght@600;700&display=swap">
<style>
  :root {
    --deep-blue: #0f56a3;
    --sky-blue: #33a4d5;
    --sun-orange: #f7941d;
    --paper: #ffffff;
    --stage: #3b3b3b;
    --text-light: #ffffff;
  }
  * { margin: 0; padding: 0; box-sizing: border-box; }
  html, body { width: 1105px; height: 1200px; overflow: hidden; }
  body { background: var(--stage); position: relative; font-family: "Questrial", sans-serif; }

  .card {
    position: absolute;
    left: 196px;
    width: 720px;
    height: 410px;
    overflow: hidden;
  }
  .card--front { top: 146px; background: var(--paper); }
  .card--back { top: 602px; background: var(--deep-blue); }

  .front-waves { position: absolute; inset: 0; width: 100%; height: 100%; }

  .brand-art {
    position: absolute;
    left: 449px; top: 35px; width: 221px; height: 104px;
    background: linear-gradient(180deg, #f7941d 0%, #33a4d5 35%, #9aa3ad 70%, #33a4d5 100%);
    border-radius: 4px;
  }
  .brand-name {
    position: absolute;
    left: 430px; top: 142px; width: 260px;
    text-align: center;
    color: var(--deep-blue);
    font-family: "Montserrat", sans-serif;
    font-weight: 700;
    line-height: 1;
  }
  .brand-name__main { display: block; font-size: 38px; letter-spacing: 0.5px; }
  .brand-name__sub { display: block; font-size: 15px; margin-top: 8px; }

  .contact { position: absolute; left: 35px; top: 252px; color: var(--text-light); font-size: 18px; }
  .contact__address { line-height: 23px; margin-bottom: 8px; }
  .contact__row { display: flex; align-items: center; height: 28px; }
  .contact__icon { width: 17px; height: 17px; margin-right: 10px; flex: none; }

  .person { position: absolute; right: 45px; top: 298px; text-align: right; color: var(--text-light); }
  .person__name { font-family: "Montserrat", sans-serif; font-weight: 700; font-size: 23px; letter-spacing: 0.3px; }
  .person__role { font-size: 20px; margin-top: 6px; margin-right: 0; }

  .back-art {
    position: absolute;
    left: 177px; top: 95px; width: 387px; height: 187px;
    background: linear-gradient(180deg, #f7941d 0%, #33a4d5 30%, #a9afb6 65%, #33a4d5 100%);
    border-radius: 4px;
  }
  .social { position: absolute; left: 0; top: 329px; width: 100%; height: 30px; }
</style>
</head>
<body>

<section class="card card--front">
  <svg class="front-waves" viewBox="0 0 521 297" preserveAspectRatio="none" aria-hidden="true">
    <path d="M0,158 C60,132 150,128 250,150 C200,140 90,142 0,168 Z" fill="var(--sun-orange)"/>
    <path d="M0,170 C120,150 230,168 310,176 C400,184 470,172 521,152 L521,160 C470,180 400,190 310,182 C230,176 120,160 0,178 Z" fill="var(--sky-blue)"/>
    <path d="M0,178 C120,160 230,176 310,182 C400,190 470,180 521,160 L521,297 L0,297 Z" fill="var(--deep-blue)"/>
  </svg>

  <div class="brand-art" role="img" aria-label="Illustration of a water taxi boat sailing before blue mountains and an orange sun"></div>
  <div class="brand-name">
    <span class="brand-name__main">MARROWBY</span>
    <span class="brand-name__sub">Water Taxi &amp; Transport</span>
  </div>

  <div class="contact">
    <p class="contact__address">214 Harbor View Road<br>Marrowby, Alaska 99615</p>
    <p class="contact__row">
      <svg class="contact__icon" viewBox="0 0 24 24" aria-hidden="true"><path fill="#fff" d="M6.6 10.8a15 15 0 0 0 6.6 6.6l2.2-2.2a1 1 0 0 1 1-.25 11.4 11.4 0 0 0 3.6.57 1 1 0 0 1 1 1V20a1 1 0 0 1-1 1A17 17 0 0 1 3 4a1 1 0 0 1 1-1h3.5a1 1 0 0 1 1 1c0 1.25.2 2.45.57 3.57a1 1 0 0 1-.25 1z"/></svg>
      907 555 0148
    </p>
    <p class="contact__row">
      <svg class="contact__icon" viewBox="0 0 24 24" aria-hidden="true"><rect x="2" y="5" width="20" height="14" rx="1.5" fill="#fff"/><path d="M3 6l9 7 9-7" stroke="var(--deep-blue)" stroke-width="1.6" fill="none"/></svg>
      mason@marrowbyferryline.com
    </p>
    <p class="contact__row">
      <svg class="contact__icon" viewBox="0 0 24 24" aria-hidden="true"><circle cx="12" cy="12" r="10" fill="#fff"/><path d="M2 12h20M12 2c3 3 3 17 0 20M12 2c-3 3-3 17 0 20" stroke="var(--deep-blue)" stroke-width="1.4" fill="none"/></svg>
      www.marrowbyferryline.com
    </p>
  </div>

  <div class="person">
    <p class="person__name">MASON ELWICK</p>
    <p class="person__role">Captain</p>
  </div>
</section>

<section class="card card--back">
  <div class="back-art" role="img" aria-label="Illustration of a water taxi boat on waves before blue mountains and an orange sun"></div>
  <svg class="social" viewBox="0 0 720 30" aria-hidden="true">
    <line x1="218" y1="15" x2="301" y2="15" stroke="#ffffff" stroke-opacity="0.7" stroke-width="1.5"/>
    <line x1="405" y1="15" x2="494" y2="15" stroke="#ffffff" stroke-opacity="0.7" stroke-width="1.5"/>
    <circle cx="319" cy="15" r="15" fill="#ffffff"/>
    <circle cx="354" cy="15" r="15" fill="#ffffff"/>
    <circle cx="389" cy="15" r="15" fill="#ffffff"/>
  </svg>
</section>

</body>
</html>
```